Website Landing Page for Medical Recruitment

Looking for a landing page to add to our existing website. The objective of the page is to recruit new clinical staff for various departments within Pinecrest Medical Center (non-profit hospital in the Richmond, TX area).

We would like the page to be modern, professional, and non-cluttered. Please include call-to-actions and include a button that will navigate to the page where candidates can submit their applications (this page already exists).

Target Market(s)

25-35-year-olds who live in the Houston and Richmond area with medical experience.

Industry/Entity Type

Medical/Health

Font styles to use
Sans Serif

Colors
0054AA
0677BA
7BADD7
CADEEF
E8F1F8

Requirements
Must have
• A "call to action"; a button that navigates to pinecrestmedhub.example/careers

```html
<!DOCTYPE html>
<html lang="en">
<head>
<meta charset="utf-8">
<title>Pinecrest Medical Center – Careers</title>
<link href="https://fonts.googleapis.com/css2?family=Cinzel:wght@500;600&family=Poppins:wght@300;400;500&display=swap" rel="stylesheet">
<style>
:root{
  --navy:#2c5f9e;
  --blue:#0054aa;
  --mid:#0677ba;
  --sky:#7badd7;
  --pale:#cadeef;
  --wash:#eef5fc;
  --text:#555b66;
  --white:#fff;
}
*{margin:0;padding:0;box-sizing:border-box}
html,body{width:1200px;height:3942px;overflow:hidden}
body{position:relative;font-family:'Poppins',sans-serif;font-weight:300;color:var(--text);background:var(--white);font-size:13.5px;line-height:1.68}
.abs{position:absolute}
a{color:inherit;text-decoration:none}
h1,h2{font-family:'Cinzel',serif;font-weight:500;color:var(--navy);letter-spacing:1px}
h2{font-size:34px;line-height:1.2}
.btn{position:absolute;display:flex;align-items:center;justify-content:center;border-radius:20px;font-size:13px;font-weight:400;letter-spacing:.3px;text-transform:uppercase}
.btn-solid{background:var(--navy);color:var(--white)}
.btn-line{border:1.5px solid var(--navy);color:var(--navy);background:var(--white)}
.btn-white{background:var(--white);color:var(--navy)}
.photo{position:absolute;border-radius:50%;overflow:hidden}
.brand{display:flex;align-items:center;gap:12px;font-family:'Poppins',sans-serif;font-weight:500;font-size:24px;color:var(--navy)}
.brand-dot{width:40px;height:40px;border-radius:50%;background:var(--navy)}
/* header */
.nav{position:absolute;top:28px;left:622px;display:flex;gap:37px;font-size:14px;color:#555}
.nav .on{color:var(--navy);font-weight:400}
/* cards */
.job{position:absolute;top:790px;width:251px;height:215px;border:1.5px solid var(--sky);border-radius:6px;background:var(--white);text-align:center;padding:24px 20px 0}
.job h3{font-weight:500;font-size:17px;color:#222}
.job .sub{color:var(--mid);font-size:13.5px;margin:4px 0 8px}
.job p{font-size:13.5px}
.job .more{margin-top:16px;font-size:13px;color:var(--navy);text-transform:uppercase}
.job.active{background:var(--navy);border-color:var(--navy);color:var(--white)}
.job.active h3,.job.active .sub,.job.active .more{color:var(--white)}
.slide-arrow{position:absolute;width:34px;height:34px;border-radius:50%;display:flex;align-items:center;justify-content:center}
/* features */
.feature{position:absolute;top:1900px;text-align:center;font-size:15px;color:#555}
.feature svg{display:block;margin:0 auto 10px}
/* news */
.news{position:absolute;top:3056px;width:340px}
.news .img{height:225px;border-radius:6px;position:relative}
.news .date{position:absolute;top:0;left:0;background:var(--navy);color:var(--white);font-size:17px;line-height:1.3;padding:6px 12px;border-radius:6px 0 6px 0;font-weight:400}
.news h3{font-weight:400;color:var(--mid);font-size:18px;line-height:1.55;margin:12px 0 14px}
.news p{font-size:13.5px}
.news .more{margin-top:12px;font-size:13px;color:var(--navy);font-weight:500;text-transform:uppercase}
/* footer */
footer{position:absolute;top:3568px;left:0;width:1200px;height:374px;background:var(--navy);color:var(--white)}
.foot-nav{position:absolute;top:147px;left:0;width:1200px;display:flex;justify-content:center;gap:38px;font-size:12.5px}
.contact{position:absolute;top:222px;text-align:center;font-size:12.5px}
.icon-c{width:36px;height:36px;border-radius:50%;background:var(--white);margin:0 auto 10px;display:flex;align-items:center;justify-content:center}
.social{position:absolute;top:3878px;display:flex;gap:19px;left:536px}
.social span{width:30px;height:30px;border-radius:50%;border:1.5px solid var(--white);display:flex;align-items:center;justify-content:center}
.social span i{width:10px;height:10px;border-radius:50%;background:var(--white);display:block}
</style>
</head>
<body>

<!-- Header -->
<header>
  <div class="abs brand" style="top:16px;left:60px"><span class="brand-dot"></span>Pinecrest Medical Center</div>
  <nav class="nav"><a class="on" href="#">Home</a><a href="#">About Us</a><a href="#">Vacancies</a><a href="#">Contact Us</a></nav>
  <a class="btn btn-solid" href="https://pinecrestmedhub.example/careers" style="top:18px;left:1017px;width:123px;height:38px">Apply Now</a>
</header>

<!-- Hero -->
<section class="abs" style="top:75px;left:0;width:1200px;height:563px;background:var(--wash)">
  <h1 class="abs" style="top:135px;left:62px;font-size:51px;line-height:1.15">NEW OFFERS ARE<br>WAITING FOR YOU</h1>
  <p class="abs" style="top:260px;left:62px;width:520px;font-size:14px">Lorem Ipsum is simply dummy text of the printing and typesetting industry. Lorem Ipsum has been the industry's standard dummy text ever since the 1500s.</p>
  <a class="btn btn-solid" href="https://pinecrestmedhub.example/careers" style="top:382px;left:60px;width:122px;height:37px">Apply Now</a>
  <a class="btn btn-line" href="#" style="top:382px;left:197px;width:191px;height:37px">View Our Vacancies</a>
  <svg class="abs" style="top:82px;left:577px" width="60" height="60" viewBox="0 0 60 60"><path d="M22 4h16v18h18v16H38v18H22V38H4V22h18z" fill="none" stroke="var(--sky)" stroke-width="4"/></svg>
  <svg class="abs" style="top:250px;left:1128px" width="60" height="60" viewBox="0 0 60 60"><path d="M22 4h16v18h18v16H38v18H22V38H4V22h18z" fill="none" stroke="var(--sky)" stroke-width="4"/></svg>
  <svg class="abs" style="top:425px;left:616px" width="54" height="54" viewBox="0 0 60 60"><path d="M22 4h16v18h18v16H38v18H22V38H4V22h18z" fill="none" stroke="var(--sky)" stroke-width="4"/></svg>
  <div class="photo" role="img" aria-label="Smiling doctor walking with medical team in a hospital corridor" style="top:57px;left:667px;width:450px;height:450px;border:3px solid var(--navy);background:linear-gradient(160deg,#e6ecf2,#c9d4de 60%,#a9b6c3)"></div>
  <div class="abs" style="top:335px;left:990px;width:130px;height:130px;border-radius:50%;background:var(--navy)"></div>
</section>

<!-- Job offers -->
<h2 class="abs" style="top:712px;left:0;width:1200px;text-align:center">JOB OFFERS</h2>
<div class="abs" style="top:758px;left:575px;width:120px;height:2px;background:var(--sky)"></div>
<div class="job" style="left:60px"><h3>Job Position</h3><div class="sub">Lorem Ipsum</div><p>Lorem Ipsum is simply dummy text of the printing and typesetting industry.</p><div class="more">Read More &rarr;</div></div>
<div class="job active" style="left:335px"><h3>Job Position</h3><div class="sub">Lorem Ipsum</div><p>Lorem Ipsum is simply dummy text of the printing and typesetting industry.</p><div class="more">Read More &rarr;</div></div>
<div class="job" style="left:612px"><h3>Job Position</h3><div class="sub">Lorem Ipsum</div><p>Lorem Ipsum is simply dummy text of the printing and typesetting industry.</p><div class="more">Read More &rarr;</div></div>
<div class="job" style="left:889px"><h3>Job Position</h3><div class="sub">Lorem Ipsum</div><p>Lorem Ipsum is simply dummy text of the printing and typesetting industry.</p><div class="more">Read More &rarr;</div></div>
<div class="slide-arrow" style="top:881px;left:42px;background:var(--navy)"><svg width="12" height="12" viewBox="0 0 12 12"><path d="M8 1L3 6l5 5" stroke="#fff" stroke-width="1.5" fill="none"/></svg></div>
<div class="slide-arrow" style="top:881px;left:1122px;background:#555"><svg width="12" height="12" viewBox="0 0 12 12"><path d="M4 1l5 5-5 5" stroke="#fff" stroke-width="1.5" fill="none"/></svg></div>

<!-- About -->
<section>
  <div class="abs" style="top:1094px;left:0;width:560px;height:462px;background:var(--wash)"></div>
  <div class="photo" role="img" aria-label="Medical staff reviewing a folder while walking down a hospital hallway" style="top:1096px;left:59px;width:458px;height:458px;background:linear-gradient(150deg,#dfe7ee,#b9c6d3 55%,#8fa1b3)"></div>
  <div class="abs" style="top:1165px;left:446px;width:46px;height:46px;border-radius:50%;background:var(--navy);display:flex;align-items:center;justify-content:center"><svg width="16" height="18" viewBox="0 0 16 18"><path d="M2 1l13 8-13 8z" fill="#fff"/></svg></div>
  <h2 class="abs" style="top:1148px;left:586px">ABOUT US</h2>
  <div class="abs" style="top:1198px;left:586px;width:555px;font-size:13.5px">
    <p>Lorem Ipsum is simply dummy text of the printing and typesetting industry. Lorem Ipsum has been the industry's standard dummy text ever since the 1500s, when an unknown printer took a galley of type and scrambled it to make a type specimen book. It has survived not only five centuries, but also the leap into electronic typesetting, remaining essentially unchanged.</p>
    <p style="margin-top:22px">It was popularised in the 1960s with the release of Letraset sheets containing Lorem Ipsum passages, and more recently with desktop publishing.</p>
  </div>
  <a class="btn btn-solid" href="https://pinecrestmedhub.example/careers" style="top:1432px;left:585px;width:123px;height:37px">Apply Now</a>
</section>

<!-- Reach your dream -->
<section>
  <div class="abs" style="top:1611px;left:964px;width:236px;height:464px;background:var(--wash)"></div>
  <h2 class="abs" style="top:1647px;left:62px">REACH YOUR DREAM</h2>
  <div class="abs" style="top:1690px;left:62px;width:475px;font-size:13.5px">
    <p>Lorem Ipsum is simply dummy text of the printing and typesetting industry. Lorem Ipsum has been the industry's standard dummy text ever since the 1500s.</p>
    <p style="margin-top:6px;font-weight:400;color:#333">Lorem Ipsum - &nbsp;is simply - dummy text.</p>
    <p style="margin-top:8px">Lorem Ipsum is simply dummy text of the printing and typesetting industry. Lorem Ipsum has been the industry's standard dummy text ever since the 1500s, when an unknown printer took a galley of type and scrambled it to make a type specimen book. <a href="#" style="font-weight:500;color:#333;text-decoration:underline">READ MORE</a></p>
  </div>
  <div class="feature" style="left:60px;width:135px"><svg width="28" height="38" viewBox="0 0 28 38"><rect x="3" y="4" width="22" height="32" rx="2" fill="none" stroke="var(--navy)" stroke-width="2"/><rect x="9" y="1" width="10" height="6" rx="1" fill="var(--navy)"/><circle cx="14" cy="17" r="4" fill="none" stroke="var(--navy)" stroke-width="2"/><path d="M8 28h12M8 32h12" stroke="var(--sky)" stroke-width="2"/></svg>Daily supply work</div>
  <div class="feature" style="left:230px;width:130px"><svg width="40" height="38" viewBox="0 0 40 38"><circle cx="20" cy="19" r="16" fill="none" stroke="var(--navy)" stroke-width="2" stroke-dasharray="70 6"/><circle cx="20" cy="19" r="10" fill="none" stroke="var(--sky)" stroke-width="2"/><path d="M20 13v12M17 16h5a2 2 0 010 4h-4a2 2 0 000 4h5" stroke="var(--navy)" stroke-width="1.8" fill="none"/></svg>Long-term roles</div>
  <div class="feature" style="left:398px;width:150px"><svg width="40" height="38" viewBox="0 0 40 38"><circle cx="15" cy="10" r="7" fill="none" stroke="var(--navy)" stroke-width="2"/><path d="M2 34c0-9 6-14 13-14s9 3 10 5" fill="none" stroke="var(--navy)" stroke-width="2"/><rect x="22" y="26" width="16" height="10" rx="1" fill="none" stroke="var(--sky)" stroke-width="2"/><path d="M22 27l8 5 8-5" stroke="var(--sky)" stroke-width="2" fill="none"/></svg>A permanent job</div>
  <a class="btn btn-solid" href="#" style="top:2020px;left:60px;width:148px;height:37px">Discover More</a>
  <div class="photo" role="img" aria-label="Young doctor with a stethoscope holding a clipboard, colleagues in the background" style="top:1615px;left:682px;width:458px;height:458px;background:linear-gradient(140deg,#e8ecf0,#cdd5dd 55%,#a7b2bd)"></div>
</section>

<!-- Vacancies band -->
<section class="abs" style="top:2157px;left:0;width:1200px;height:322px;background:var(--navy);color:var(--white)">
  <div class="abs" style="top:50px;left:60px;width:215px;height:215px;border-radius:50%;background:var(--white)"></div>
  <h2 class="abs" style="top:57px;left:400px;color:var(--white)">OUR VACANCIES</h2>
  <p class="abs" style="top:104px;left:400px;width:740px;font-size:13.5px">Lorem Ipsum is simply dummy text of the printing and typesetting industry. Lorem Ipsum has been the industry's standard dummy text ever since the 1500s, when an unknown printer took a galley of type and scrambled it to make a type specimen book. It has survived not only five centuries, but also the leap into electronic typesetting, remaining essentially unchanged.</p>
  <a class="btn btn-white" href="https://pinecrestmedhub.example/careers" style="top:231px;left:399px;width:123px;height:37px">Apply Now</a>
</section>

<!-- Testimonials -->
<section>
  <h2 class="abs" style="top:2555px;left:0;width:1200px;text-align:center">WHAT OUR CLIENT SAYS</h2>
  <div class="photo" role="img" aria-label="Portrait of a client in a dark blazer" style="top:2638px;left:263px;width:178px;height:178px;background:linear-gradient(160deg,#eceef0,#c8ccd2 60%,#3a3f4a)"></div>
  <div class="abs" style="top:2631px;left:257px;width:62px;height:62px;border-radius:50%;background:var(--navy);display:flex;align-items:center;justify-content:center"><svg width="30" height="24" viewBox="0 0 30 24"><path d="M2 22V13C2 6 6 2 12 1v5c-3 1-5 3-5 6h5v10zM17 22V13c0-7 4-11 10-12v5c-3 1-5 3-5 6h5v10z" fill="#fff"/></svg></div>
  <p class="abs" style="top:2636px;left:513px;width:470px;font-size:13.5px">Lorem Ipsum is simply dummy text of the printing and typesetting industry. Lorem Ipsum has been the industry's standard dummy text ever since the 1500s, when an unknown printer took a galley of type and scrambled it to make a type specimen book. It has survived not only five centuries, but also the leap into electronic typesetting, remaining essentially unchanged.</p>
  <div class="abs" style="top:2784px;left:513px;font-size:13.5px;font-weight:500;color:var(--navy)">CLIENT NAME</div>
  <div class="abs" style="top:2822px;left:511px;width:50px;height:30px;border-radius:15px;background:var(--navy);display:flex;align-items:center;justify-content:center"><svg width="26" height="10" viewBox="0 0 26 10"><path d="M25 5H2M6 1L2 5l4 4" stroke="#fff" stroke-width="1.8" fill="none"/></svg></div>
  <div class="abs" style="top:2822px;left:576px;width:50px;height:30px;border-radius:15px;background:var(--pale);display:flex;align-items:center;justify-content:center"><svg width="26" height="10" viewBox="0 0 26 10"><path d="M1 5h23M20 1l4 4-4 4" stroke="var(--navy)" stroke-width="1.8" fill="none"/></svg></div>
</section>

<!-- Latest news -->
<section class="abs" style="top:2935px;left:0;width:1200px;height:633px;background:var(--wash)">
  <h2 style="position:absolute;top:47px;left:0;width:1200px;text-align:center">LATEST NEWS</h2>
</section>
<article class="news" style="left:61px"><div class="img" role="img" aria-label="Doctors reviewing documents on a staircase" style="background:linear-gradient(150deg,#d9cfc2,#b7ad9f 50%,#8e8f96)"><div class="date">6<br>July</div></div><h3>Lorem Ipsum is simply dummy text of the printing.</h3><p>Lorem Ipsum is simply dummy text of the printing and typesetting industry.</p><div class="more">Read More &rarr;</div></article>
<article class="news" style="left:431px"><div class="img" role="img" aria-label="Medical team rushing a patient through a hospital" style="background:linear-gradient(150deg,#e3eef0,#b7d0d6 50%,#5d8fa3)"><div class="date">6<br>July</div></div><h3>Lorem Ipsum is simply dummy text of the printing.</h3><p>Lorem Ipsum is simply dummy text of the printing and typesetting industry.</p><div class="more">Read More &rarr;</div></article>
<article class="news" style="left:800px"><div class="img" role="img" aria-label="Group of doctors and nurses standing together" style="background:linear-gradient(150deg,#c4ccd6,#93a4b8 50%,#2f5d96)"><div class="date">6<br>July</div></div><h3>Lorem Ipsum is simply dummy text of the printing.</h3><p>Lorem Ipsum is simply dummy text of the printing and typesetting industry.</p><div class="more">Read More &rarr;</div></article>
<a class="btn btn-solid" href="#" style="top:3481px;left:519px;width:162px;height:36px">View More Posts</a>

<!-- Footer -->
<footer>
  <div class="brand" style="position:absolute;top:55px;left:0;width:1200px;justify-content:center;color:var(--white)"><span class="brand-dot" style="background:var(--white)"></span>Pinecrest Medical Center</div>
  <nav class="foot-nav"><a href="#">Home</a><a href="#">About Us</a><a href="#">Vacancies</a><a href="#">Contact Us</a></nav>
  <div class="contact" style="left:260px;width:275px"><div class="icon-c"><svg width="14" height="18" viewBox="0 0 14 18"><path d="M7 17s6-6 6-10A6 6 0 001 7c0 4 6 10 6 10z" fill="var(--navy)"/><circle cx="7" cy="7" r="2" fill="#fff"/></svg></div>Lorem Ipsum is simply dummy text of the.</div>
  <div class="contact" style="left:540px;width:150px;font-weight:500"><div class="icon-c"><svg width="16" height="16" viewBox="0 0 16 16"><path d="M3 1l3 3-2 2c1 2 3 4 5 5l2-2 3 3-2 3C7 15 1 9 1 3z" fill="var(--navy)"/></svg></div>123 456 7890</div>
  <div class="contact" style="left:690px;width:215px"><div class="icon-c"><svg width="16" height="12" viewBox="0 0 16 12"><rect x="1" y="1" width="14" height="10" fill="var(--navy)"/><path d="M1 1l7 6 7-6" stroke="#fff" fill="none"/></svg></div>info@pinecrestmedhub.example</div>
  <div style="position:absolute;top:345px;left:0;width:1200px;height:1px;background:rgba(255,255,255,.4)"></div>
  <div style="position:absolute;top:352px;left:0;width:1200px;text-align:center;font-size:11.5px">© PINECREST MEDICAL CENTER - 2022. All Rights Reserved.</div>
</footer>
<div class="social"><span><i></i></span><span><i></i></span><span><i></i></span></div>

</body>
</html>
```